Business Card Design

We need a business card designed for our new company. Prefer a black card with white logo & writing.

Contact Information for Business Card

Ted Galloway, address: 7-4812 Fernhollow Road, Abbotsford, BC, V3K 8R2, Office Phone: 604-712-3390, Cell: 604-947-2164, Email: ted@resinworkshub.ca

Colors

Designer to choose only greyscale colors for use in the design.

```html
<!DOCTYPE html>
<html lang="en">
<head>
<meta charset="utf-8">
<title>Resin Works Hub – Business Card</title>
<link href="https://fonts.googleapis.com/css2?family=Montserrat:wght@400;700;800&display=swap" rel="stylesheet">
<style>
  :root {
    --backdrop: #d9d9d9;
    --card-front: #222222;
    --card-back: #1a1a1a;
    --ink-white: #ffffff;
    --ink-muted: #bdbdbd;
    --ink-gloss: #0d0d0d;
    --shadow: rgba(0,0,0,0.35);
  }
  * { margin: 0; padding: 0; box-sizing: border-box; }
  html, body {
    width: 1200px; height: 786px; overflow: hidden;
    background: var(--backdrop);
    font-family: "Montserrat", sans-serif;
  }
  .stage {
    position: relative; width: 1200px; height: 786px;
    display: flex; align-items: center; justify-content: center; gap: 40px;
  }
  .card {
    position: relative; width: 540px; height: 309px;
    box-shadow: 0 10px 28px var(--shadow);
  }
  .card--front { background: var(--card-front); color: var(--ink-white); }
  .card--back { background: var(--card-back); }

  .holder { position: absolute; left: 46px; top: 44px; }
  .holder__name { font-weight: 700; font-size: 19px; letter-spacing: 0.3px; }
  .holder__role { font-weight: 400; font-size: 11px; color: var(--ink-muted); margin-top: 4px; }

  .brand {
    position: absolute; text-align: center;
    font-weight: 800; text-transform: uppercase; line-height: 1;
    display: flex; align-items: center; gap: 12px;
  }
  .brand__mark { width: 14px; height: 14px; background: currentColor; flex: none; }
  .brand__name { font-size: 34px; letter-spacing: 0.5px; }
  .card--front .brand { right: 40px; top: 98px; color: var(--ink-white); }
  .card--back .brand {
    left: 50%; top: 50%; transform: translate(-50%, -50%);
    color: var(--ink-gloss);
  }

  .contact {
    position: absolute; left: 46px; top: 160px;
    font-size: 12px; font-weight: 400; line-height: 18px; color: var(--ink-white);
  }
  .contact__address { margin-bottom: 8px; }
  .contact__list { list-style: none; }
  .contact__item { display: flex; align-items: center; gap: 10px; }
  .contact__icon { width: 11px; height: 11px; fill: var(--ink-white); flex: none; }
</style>
</head>
<body>
<main class="stage">
  <section class="card card--front">
    <div class="holder">
      <div class="holder__name">Ted Galloway</div>
      <div class="holder__role">owner</div>
    </div>

    <div class="brand">
      <span class="brand__mark"></span>
      <span class="brand__name">Resin Works<br>Hub</span>
    </div>

    <div class="contact">
      <div class="contact__address">7-4812 Fernhollow Road,<br>Abbotsford, BC, V3K 8R2</div>
      <ul class="contact__list">
        <li class="contact__item">
          <svg class="contact__icon" viewBox="0 0 12 12"><path d="M2.4 0.8 4.3 2.7 3.3 4.3c.7 1.6 2 2.9 3.6 3.6l1.6-1 1.9 1.9-1.2 1.9C5.1 10.6 0.8 6.300 1 2z"/></svg>
          <span>604-712-3390</span>
        </li>
        <li class="contact__item">
          <svg class="contact__icon" viewBox="0 0 12 12"><path d="M3 0h6a1 1 0 0 1 1 1v10a1 1 0 0 1-1 1H3a1 1 0 0 1-1-1V1a1 1 0 0 1 1-1zm0.8 1.4v7.6h4.4V1.4zM6 9.6a.7.7 0 1 0 0 1.4.7.7 0 0 0 0-1.4z"/></svg>
          <span>604-947-2164</span>
        </li>
        <li class="contact__item">
          <svg class="contact__icon" viewBox="0 0 12 12"><path d="M0 2.5h12v7H0zM0.8 3.1 6 6.6l5.2-3.5v-0.1H0.8z" fill-rule="evenodd"/></svg>
          <span>ted@resinworkshub.ca</span>
        </li>
        <li class="contact__item">
          <svg class="contact__icon" viewBox="0 0 12 12"><circle cx="6" cy="6" r="5.5" fill="none" stroke="#fff" stroke-width="1"/><path d="M0.5 6h11M6 0.5c-2.4 3-2.4 8 0 11M6 0.5c2.4 3 2.4 8 0 11" fill="none" stroke="#fff" stroke-width="0.9"/></svg>
          <span>www.resinworkshub.ca</span>
        </li>
      </ul>
    </div>
  </section>

  <section class="card card--back">
    <div class="brand">
      <span class="brand__mark"></span>
      <span class="brand__name">Resin Works<br>Hub</span>
    </div>
  </section>
</main>
</body>
</html>
```